San Francisco Leading Consulting firm - 47Vora Web Design Project

•Create a Web Design
•Uncoded webpage layout design
•2 Pages Design - Homepage + Interior Page

Task Description
Hello, we're looking for a re-design our current website www.47vora-example.com

we have a sample mockup design @

http://47vora.pubtrellis-example.org/

This shows the layout that we like and also a sample of 6 pictures that would change based on where you mouse over..

6 pictures HOME design needs to be included.

SMART
THOUGHTFUL
FLEXIBLE
CREATIVE SERVICES
TECHNICAL SERVICES
PARTNERS

sites we like:

http://www.melvanadvisory-example.com/Home.cfm?id=Home
http://www.plinthworks-example.com/index.html

Our company can be best described as: 100+ employees, cutting-edge, depandable, innovative, strong, smart.

Our Primary focus is: IT Consulting Services and Creative Design services

47Vora LLC is a consulting firm providing creative design, business and technology solutions to both private and public interests.

Established in 1996, 47Vora is a San Francisco based company providing specialists for a range of business needs including:

Creative Design Services
•Print
•Logo Design
•Website Design
•Illustration

and

Business and Technology solutions

•Application Software and Web Development
•Business Process Re-Design (BPR)
•Business/Systems Analysis and Requirement Documentation
•Mentoring and Training
•Network/Hardware Installation Services
•System Design and Architecture
•Vendor Management
•Docuvault Architecture and Implementation

our sample mockup site:

Reason: Due to holiday season, we're not available to work with designers and finilize our design.  

Thank you very much for submitting your design.

We appreciate your time and creativity.   Since, our office is currently closed for holidays, we will be reviewing it in details next week and will make our decision as soon as possible.

It would be great if you could submit any of your changes by Wed next week, so it would be part of our reviews. 

Please see updated wireframe under attachments:  we have some minor updates to our wireframe that we would like you to update your designs, if possible.  

We also encorouge you not to use our standard wireframe and come up with more unique designs.   Everything would be considered when we review your design.

 

Pellam Market(s)

Creative services and professional services clients, including government agencies

Industry/Entity Type

Business

Requirements
Must have
• Clean, professional look, easy navigation

```html
<!DOCTYPE html>
<html lang="en">
<head>
<meta charset="utf-8">
<title>47Vora — Home</title>
<link href="https://fonts.googleapis.com/css2?family=Arimo:wght@400;700&family=Barlow+Condensed:ital,wght@0,600;1,400&display=swap" rel="stylesheet">
<style>
:root{
  --green:#5cb814;
  --green-bright:#7ed321;
  --ink:#333;
  --muted:#777;
  --line:#c9c9c9;
  --white:#fff;
  --black:#000;
}
*{box-sizing:border-box;margin:0;padding:0}
html,body{width:1200px;height:1100px;overflow:hidden;background:var(--white)}
body{position:relative;font-family:Arimo,Arial,sans-serif;color:var(--ink)}
.abs{position:absolute}
/* header */
.site-header{position:absolute;left:0;top:0;width:1200px;height:98px;border-bottom:1px solid #888}
.brand{position:absolute;left:132px;top:26px;display:flex;align-items:center;gap:10px}
.brand-dot{width:34px;height:34px;border-radius:50%;background:var(--green)}
.brand-name{font-size:30px;color:#666;letter-spacing:1px}
.contact{position:absolute;top:4px;font-size:12px;line-height:18px;color:var(--muted)}
.contact-address{left:813px}
.contact-direct{left:962px;color:var(--green);font-weight:700}
.main-nav{position:absolute;top:69px;left:429px;display:flex;gap:36px;font-size:13.5px;color:#444}
.main-nav .is-active{color:var(--green);position:relative}
.main-nav .is-active::after{content:"";position:absolute;left:50%;top:20px;margin-left:-5px;border:5px solid transparent;border-bottom:7px solid var(--green);border-top:0}
/* hero */
.hero-bg{position:absolute;left:0;top:98px;width:1200px;height:569px;background:linear-gradient(180deg,#e6e6e6 0%,#bdbdbd 45%,#6f6f6f 80%,#8a8a8a 100%)}
.slide{position:absolute;left:139px;top:160px;width:920px;height:329px;background:var(--black);border-radius:8px 8px 0 0;overflow:hidden}
.slide-photo{position:absolute;right:0;top:0;width:420px;height:329px;background:linear-gradient(90deg,#000 0%,#3a3a3a 40%,#8d8d8d 70%,#5a5a5a 100%)}
.slide-copy{position:absolute;left:81px;top:102px;font-family:"Barlow Condensed","Arial Narrow",sans-serif;line-height:1}
.slide-copy .l1{font-size:41px;font-weight:600;color:var(--white)}
.slide-copy .l2{font-size:52px;font-weight:600;color:var(--green-bright);margin-top:-4px}
.slide-copy .l3{font-size:26px;font-style:italic;color:var(--white);margin-top:2px}
.slider-arrow{position:absolute;top:302px;width:32px;height:64px;background:var(--white)}
.slider-arrow.prev{left:107px;border-radius:32px 0 0 32px}
.slider-arrow.next{left:1059px;border-radius:0 32px 32px 0}
.slider-arrow svg{position:absolute;top:16px}
.slider-dots{position:absolute;left:519px;top:498px;display:flex;gap:12px;align-items:center}
.slider-dots span{width:15px;height:15px;border-radius:50%;background:var(--white)}
.slider-dots .is-current{width:20px;height:20px;background:var(--green-bright);border:3px solid #4a8f12}
/* feature cards */
.card{position:absolute;top:603px;width:300px;height:107px;background:linear-gradient(180deg,#fff 0%,#f6f6f6 60%,#fff 100%);border-radius:6px 6px 0 0;box-shadow:0 -1px 4px rgba(0,0,0,.25)}
.card svg{position:absolute;left:28px;top:12px}
.card-title{position:absolute;top:23px;font-size:15px;font-weight:700;color:#444;line-height:18px}
.card-link{position:absolute;top:63px;font-size:11px;font-weight:700;color:var(--green)}
/* clients */
.clients-label{position:absolute;left:127px;top:767px;font-size:18px;font-weight:700;line-height:20px;color:#333}
.client{position:absolute;top:771px;font-size:14px;font-weight:700;color:#8a8a8a;display:flex;align-items:center;gap:5px}
.client i{display:block;width:10px;height:10px;border-radius:50%;background:#8a8a8a}
.vrule{position:absolute;left:875px;top:745px;width:1px;height:76px;background:var(--line)}
.latest h3{position:absolute;left:902px;top:750px;font-size:15px;font-weight:700;color:#111}
.latest .date{position:absolute;left:902px;top:774px;font-size:12px;font-weight:700;color:var(--green)}
.latest p{position:absolute;left:902px;top:789px;font-size:12.5px;line-height:16px;color:#222;width:180px}
.hrule{position:absolute;left:122px;width:960px;height:1px;background:var(--line)}
/* service lists */
.service-list{position:absolute;list-style:none;font-size:13px;line-height:24px;color:#444}
/* footer */
.copyright{position:absolute;left:119px;top:987px;font-size:12px;font-weight:700;color:#444}
.footer-nav{position:absolute;left:530px;top:987px;display:flex;gap:30px;font-size:12px;font-weight:700;color:var(--green)}
</style>
</head>
<body>
<header class="site-header">
  <div class="brand"><span class="brand-dot"></span><span class="brand-name">47Vora</span></div>
  <div class="contact contact-address">2750 Harlow St, Ste 410<br>San Francisco, CA 94107</div>
  <div class="contact contact-direct">415-555-0142<br>info@47vora-example.com</div>
  <nav class="main-nav"><span class="is-active">Home</span><span>Company</span><span>Creative Services</span><span>Technical Services</span><span>Partners</span><span>Contact Us</span></nav>
</header>

<div class="hero-bg" role="img" aria-label="Black and white aerial view of the San Francisco skyline"></div>
<div class="slide">
  <div class="slide-photo" role="img" aria-label="Businessman in a suit moving a chess piece on a board"></div>
  <div class="slide-copy"><div class="l1">WE DEVELOP</div><div class="l2">THE RIGHT STRATEGY</div><div class="l3">FOR YOUR PROJECT</div></div>
</div>
<div class="slider-arrow prev"><svg width="26" height="34" viewBox="0 0 26 34"><path d="M20 2 L6 17 L20 32" fill="none" stroke="#5cb814" stroke-width="6"/></svg></div>
<div class="slider-arrow next"><svg width="26" height="34" viewBox="0 0 26 34"><path d="M4 2 L18 17 L4 32" fill="none" stroke="#5cb814" stroke-width="6"/></svg></div>
<div class="slider-dots"><span class="is-current"></span><span></span><span></span><span></span><span></span><span></span></div>

<div class="card" style="left:129px">
  <svg width="44" height="42" viewBox="0 0 44 42"><path d="M22 38 C8 32 8 16 22 4 C36 16 36 32 22 38Z M22 38 L22 14" fill="none" stroke="#666" stroke-width="2"/></svg>
  <div class="card-title" style="left:110px">Creative Services</div>
  <div class="card-link" style="left:186px">LEARN MORE</div>
</div>
<div class="card" style="left:449px">
  <svg width="44" height="42" viewBox="0 0 44 42"><path d="M6 36 L36 6 M8 6 L36 34" stroke="#555" stroke-width="5" stroke-linecap="round"/></svg>
  <div class="card-title" style="left:120px">Business &amp; Technical<br>Services</div>
  <div class="card-link" style="left:189px">LEARN MORE</div>
</div>
<div class="card" style="left:770px">
  <svg width="44" height="42" viewBox="0 0 44 42"><circle cx="15" cy="15" r="9" fill="none" stroke="#555" stroke-width="5" stroke-dasharray="4 3"/><circle cx="30" cy="30" r="7" fill="none" stroke="#555" stroke-width="4" stroke-dasharray="3 2"/></svg>
  <div class="card-title" style="left:132px">Corporate Partners</div>
  <div class="card-link" style="left:197px">LEARN MORE</div>
</div>

<div class="clients-label">Featured<br>Clients</div>
<svg class="abs" style="left:208px;top:762px" width="28" height="48" viewBox="0 0 28 48"><path d="M2 0 L14 0 L28 24 L14 48 L2 48 L16 24Z" fill="#3a9a14"/></svg>
<div class="client" style="left:256px">Norvik</div>
<div class="client" style="left:330px"><i></i>Pellam</div>
<div class="client" style="left:405px">Quorra</div>
<div class="client" style="left:470px">Halden</div>
<div class="client" style="left:545px">Tarnley</div>
<div class="client" style="left:627px">Ovelia</div>
<div class="client" style="left:702px">Castra</div>
<div class="client" style="left:786px"><i></i>Fenwold</div>
<div class="vrule"></div>
<div class="latest">
  <h3>Latest Project</h3>
  <svg class="abs" style="left:1016px;top:750px" width="10" height="14" viewBox="0 0 10 14"><path d="M2 1 L8 7 L2 13" fill="none" stroke="#3a9a14" stroke-width="3"/></svg>
  <div class="date">JANUARY 19, 2011</div>
  <p>Lorem ipsum dolor sit amet, consectetur adipiscing elit.</p>
</div>

<div class="hrule" style="top:837px"></div>
<ul class="service-list" style="left:132px;top:855px"><li>Application Software and Web Development</li><li>Business Process Re-Design (BPR)</li><li>Systems Analysis and Requirement Docs</li><li>Mentoring and Training</li></ul>
<ul class="service-list" style="left:456px;top:853px"><li>Network/Hardware Installation Services</li><li>System Design and Architecture</li><li>Vendor Management</li><li>Docuvault Architecture and Implementation</li></ul>
<ul class="service-list" style="left:780px;top:848px"><li>Print &amp; Package Design</li><li>Brand and Identity Creation</li><li>Website and User Experience Design</li><li>Illustration Design</li></ul>
<div class="hrule" style="top:967px"></div>

<footer>
  <div class="copyright">Copyright 2011, 47Vora, LLC All rights reserved.</div>
  <nav class="footer-nav"><span>Home</span><span>Company</span><span>Technical Services</span><span>Creative Services</span><span>Partners</span><span>Contact Us</span></nav>
</footer>
</body>
</html>
```